Kestrelway Financial Plans

I am looking for a complete resdesign of my small financial presentation. This is a Word Doc/PDF that I print off when meeting with people in private. I often present my "two pager" that I have been using for years and years. It tells them the basics of what I do, how I help people and foundational financial principles.

I have recently gone out on my own in business and have completely rebranded. This presentation is my most used tool, so it is the first of many things I would like to redo. I am hoping it will somehow coordinate with the colors of my business, not necessarily the EXACT same 3 colors everywhere, but have the design colors compliment.

I've uploaded all my logo designs, as well as the current "two-pager". I am not against it going to 3 pages if needed. As it will still land on 2 pages with duplex printing.

It has always been VERY simple. I am wanting it built into a more professional and design specific format, to show off my branding, without being over cluttered.

I am completely open to ANY graphics changes. Obviously some are very novice, the house on the last page has always been overly simplified.

```html
<!DOCTYPE html>
<html lang="en">
<head>
<meta charset="utf-8">
<title>Kestrelway Financial Plans – The Financial Challenge</title>
<link href="https://fonts.googleapis.com/css2?family=Poppins:wght@600;700&family=Roboto:wght@400;500;700&display=swap" rel="stylesheet">
<style>
:root{
  --backdrop:#636466;
  --navy:#0f1e30;
  --navy-soft:#1a2c44;
  --green:#2dbd6e;
  --paper:#ffffff;
  --mist:#e8eaec;
  --ink:#1b1f24;
  --partner:#a6d3ee;
  --teal:#68b1bc;
}
*{box-sizing:border-box;margin:0;padding:0}
html,body{width:1200px;height:860px;overflow:hidden;background:var(--backdrop)}
body{position:relative;font-family:"Roboto",sans-serif;color:var(--ink)}
.page{position:absolute;width:514px;height:727px;overflow:hidden}
.page--left{left:67px;top:69px;background:var(--paper)}
.page--right{left:629px;top:71px;background:var(--mist)}
.abs{position:absolute}
.heading{font-family:"Poppins",sans-serif;font-weight:700}

/* header */
.masthead{left:0;top:0;width:514px;height:49px;background:var(--navy)}
.masthead__brand{left:0;top:0;width:240px;height:49px;background:var(--paper);clip-path:polygon(0 0,214px 0,227px 49px,0 49px)}
.masthead__stripe{left:0;top:0;width:240px;height:49px;background:var(--green);clip-path:polygon(214px 0,222px 0,235px 49px,227px 49px)}
.brandname{left:40px;top:12px;font-family:"Poppins",sans-serif;font-weight:700;color:var(--navy);text-align:center;line-height:1}
.brandname__main{font-size:17px;letter-spacing:.2px}
.brandname__sub{font-size:6.5px;letter-spacing:1.6px;margin-top:4px}
.masthead__title{left:258px;top:15px;color:#fff;font-size:14.5px}

/* challenge stats */
.challenge{left:0;top:49px;width:514px;height:312px;background:var(--mist)}
.stat-icon{width:50px;height:50px;border-radius:50%;background:var(--green);display:flex;align-items:center;justify-content:center}
.stat-label{width:100px;text-align:center;font-size:11.5px;color:var(--navy)}
.stat-rule{width:1px;background:var(--navy)}
.stat-copy{left:141px;width:345px;font-size:8.6px;line-height:12px;text-transform:uppercase;color:var(--ink)}
.stat-copy p+p{margin-top:10px}

/* services band */
.services{left:0;top:361px;width:514px;height:116px;background:var(--navy);color:#fff}
.services__title{left:0;top:16px;width:514px;text-align:center;font-size:11.5px}
.service{top:45px;width:100px;text-align:center;font-size:8.4px;text-transform:uppercase}
.service__icon{width:36px;height:36px;border-radius:50%;background:var(--green);margin:0 auto 10px;display:flex;align-items:center;justify-content:center}

/* how section */
.how__title{left:25px;top:495px;font-size:15.5px;color:var(--navy)}
.how__bar{left:26px;top:527px;width:41px;height:2px;background:var(--green)}
.pie{left:16px;top:548px}
.savings-tag{left:156px;top:612px;transform:rotate(-90deg);transform-origin:center;font-size:11.5px;color:var(--navy);width:50px;text-align:center}
.goals{left:206px;top:560px;list-style:none}
.goals li{height:31px;display:flex;align-items:center;font-size:10px;color:var(--ink)}
.goals li::before{content:"";width:9px;height:9px;border:1px solid var(--ink);margin-right:6px}
.partners{left:359px;top:492px;display:grid;grid-template-columns:68px 68px;grid-auto-rows:33px;gap:4px}
.partner{background:var(--partner);display:flex;align-items:center;justify-content:center;font-size:7.5px;font-weight:500;color:var(--navy);text-align:center;line-height:1.1}
.payus{left:399px;top:699px;font-size:11.5px;color:var(--navy)}

/* rule of 72 */
.rule{left:0;top:0;width:514px;height:263px;background:var(--navy)}
.rule__title{left:18px;top:20px;color:#fff;font-size:14.5px}
.growth{top:52px;width:117px}
.growth__table{border:1px solid #fff}
.growth__head{height:19px;background:#fff;display:flex;justify-content:space-between;align-items:center;padding:0 10px;font-size:8px;font-weight:700;color:var(--navy)}
.growth__row{height:18.5px;display:flex;justify-content:space-between;align-items:center;padding:0 10px;font-size:8px;color:#fff;border-top:1px solid #fff}
.growth__row:first-of-type{border-top:none}
.growth__note{margin-top:7px;height:32px;background:var(--navy-soft);color:#fff;font-size:5.8px;line-height:10px;text-align:center;display:flex;align-items:center;justify-content:center}

/* taxes */
.taxes__title{left:19px;top:289px;font-size:14.5px;color:var(--navy)}
.taxes__art{left:19px;top:327px;width:478px;height:138px;background:linear-gradient(135deg,#5ea9b4,var(--teal) 55%,#7cbfc8)}
.taxes__card{left:19px;top:465px;width:478px;height:177px;background:#fff}
.tax-col{top:0;height:177px;padding:20px 0 0 19px}
.tax-col + .tax-col{border-left:1.5px solid var(--green)}
.tax-col h3{font-family:"Poppins",sans-serif;font-weight:700;font-size:11px;color:var(--navy);margin-bottom:13px}
.tax-col ul{list-style:none}
.tax-col li{position:relative;padding-left:10px;font-size:6.8px;line-height:10px;text-transform:uppercase;margin-bottom:6px;color:var(--ink)}
.tax-col li::before{content:"";position:absolute;left:0;top:3px;width:4px;height:4px;border-radius:50%;background:var(--green)}
.tax-tag{position:absolute;left:19px;top:131px;height:21px;padding:0 10px;background:var(--green);color:#fff;font-family:"Poppins",sans-serif;font-weight:700;font-size:11px;line-height:21px}
.taxes__foot{left:19px;top:646px;width:478px;height:58px;background:#fff}
.foot-rule{top:14px;width:1.5px;height:30px;background:var(--green)}
.foot-text{top:17px;font-size:8.5px;font-weight:500;line-height:13px;color:var(--navy);text-transform:uppercase}
</style>
</head>
<body>

<section class="page page--left">
  <header class="abs masthead">
    <div class="abs masthead__brand"></div>
    <div class="abs masthead__stripe"></div>
    <div class="abs brandname">
      <div class="brandname__main">KESTRELWAY</div>
      <div class="brandname__sub">FINANCIAL PLANS</div>
    </div>
    <h1 class="abs heading masthead__title">THE FINANCIAL CHALLENGE</h1>
  </header>

  <div class="abs challenge"></div>

  <div class="abs stat-icon" style="left:38px;top:69px">
    <svg width="26" height="26" viewBox="0 0 26 26"><circle cx="13" cy="13" r="11" fill="#fff"/><text x="13" y="18" font-family="Roboto,sans-serif" font-size="14" font-weight="700" fill="#2dbd6e" text-anchor="middle">$</text></svg>
  </div>
  <div class="abs heading stat-label" style="left:13px;top:130px">SAVINGS</div>
  <div class="abs stat-rule" style="left:118px;top:67px;height:76px"></div>
  <div class="abs stat-copy" style="top:65px">
    <p>49% of Canadian employees are living paycheque to paycheque. 25% of Canadians are unable to cover an unexpected $500 expense-Statsline (Feb 2023)</p>
    <p>25% of Canadians need to access their retirement savings early. 20% of Canadians have no savings. 39% of Canadians aged 55-65 have less than $5,000 in savings. -National Finance Office (June 2023)</p>
  </div>

  <div class="abs stat-icon" style="left:38px;top:164px">
    <svg width="26" height="26" viewBox="0 0 26 26"><path d="M3 18h6l5 3 8-5v3l-8 5-5-2H3z" fill="#fff"/><circle cx="15" cy="9" r="6" fill="#fff"/><text x="15" y="12.5" font-family="Roboto,sans-serif" font-size="9" font-weight="700" fill="#2dbd6e" text-anchor="middle">$</text></svg>
  </div>
  <div class="abs heading stat-label" style="left:13px;top:225px">DEBT</div>
  <div class="abs stat-rule" style="left:118px;top:163px;height:78px"></div>
  <div class="abs stat-copy" style="top:162px">
    <p>The average Canadian has $22,131 in consumer debt. Which excludes mortgages.-Creditline Data (Aug 2024)</p>
    <p>Over 55% of Canadians hold credit card debt and the total Canadian household debt has increased to $2.52trillion, including consumer credit, mortgage and non-mortgage loans. -Banking Council (Aug 2024)</p>
  </div>

  <div class="abs stat-icon" style="left:37px;top:269px">
    <svg width="26" height="26" viewBox="0 0 26 26"><rect x="4" y="3" width="13" height="18" rx="2" fill="#fff"/><rect x="7" y="7" width="7" height="1.6" fill="#2dbd6e"/><rect x="7" y="11" width="7" height="1.6" fill="#2dbd6e"/><path d="M18 12l5 2v4c0 3-2 5-5 6-3-1-5-3-5-6v-4z" fill="#fff" stroke="#2dbd6e" stroke-width="1.2"/><path d="M16 18l1.5 1.5 3-3" stroke="#2dbd6e" stroke-width="1.4" fill="none"/></svg>
  </div>
  <div class="abs heading stat-label" style="left:13px;top:331px">INSURANCE</div>
  <div class="abs stat-rule" style="left:117px;top:268px;height:80px"></div>
  <div class="abs stat-copy" style="top:269px;left:140px">
    <p>45% of Canadians do not have individual life insurance coverage, but 48% say their families would face financial trouble within 6 months of losing someone. -Lifeview Research (Apr 2023)</p>
    <p>2-in-5 Canadians (43% women / 44% men) will be diagosed with a form ofcancer or other critical illness during their lifetime. Every 7 seconds.-Health Data Hub (June 2024)</p>
  </div>

  <section class="abs services">
    <h2 class="abs heading services__title">WHO ARE WE AND WHAT DO WE DO?</h2>
    <div class="abs service" style="left:-6px">
      <div class="service__icon"><svg width="22" height="22" viewBox="0 0 22 22"><circle cx="11" cy="11" r="8" fill="none" stroke="#fff" stroke-width="1.8"/><text x="11" y="15" font-family="Roboto,sans-serif" font-size="11" font-weight="700" fill="#fff" text-anchor="middle">$</text></svg></div>CASH FLOW</div>
    <div class="abs service" style="left:84px;width:110px">
      <div class="service__icon"><svg width="20" height="22" viewBox="0 0 20 22"><path d="M10 1l8 3v6c0 6-4 9-8 11-4-2-8-5-8-11V4z" fill="#fff"/><path d="M6 11l3 3 5-5" stroke="#2dbd6e" stroke-width="2" fill="none"/></svg></div>CASH FLOW PROTECTION</div>
    <div class="abs service" style="left:196px;width:90px">
      <div class="service__icon"><svg width="22" height="22" viewBox="0 0 22 22"><circle cx="8" cy="8" r="5" fill="none" stroke="#fff" stroke-width="2"/><rect x="7" y="13" width="13" height="7" fill="#fff"/></svg></div>DEBT MANAGEMENT</div>
    <div class="abs service" style="left:289px;width:90px">
      <div class="service__icon"><svg width="18" height="22" viewBox="0 0 18 22"><rect x="2" y="3" width="14" height="18" rx="3" fill="#fff"/><text x="9" y="16" font-family="Roboto,sans-serif" font-size="10" font-weight="700" fill="#2dbd6e" text-anchor="middle">$</text></svg></div>EMERGENCY FUND</div>
    <div class="abs service" style="left:362px;width:100px">
      <div class="service__icon"><svg width="22" height="22" viewBox="0 0 22 22"><ellipse cx="8" cy="6" rx="6" ry="2.5" fill="#fff"/><ellipse cx="8" cy="11" rx="6" ry="2.5" fill="#fff"/><ellipse cx="8" cy="16" rx="6" ry="2.5" fill="#fff"/><circle cx="16" cy="14" r="5" fill="#fff" stroke="#2dbd6e" stroke-width="1"/></svg></div>BUILD WEALTH</div>
    <div class="abs service" style="left:428px;width:90px">
      <div class="service__icon"><svg width="20" height="22" viewBox="0 0 20 22"><path d="M10 1l8 3v6c0 6-4 9-8 11-4-2-8-5-8-11V4z" fill="none" stroke="#fff" stroke-width="2"/><path d="M6 11l3 3 5-5" stroke="#fff" stroke-width="2" fill="none"/></svg></div>PRESERVE</div>
  </section>

  <h2 class="abs heading how__title">HOW ARE WE DOING IT?</h2>
  <div class="abs how__bar"></div>

  <svg class="abs pie" width="140" height="140" viewBox="0 0 140 140" role="img" aria-label="Pie chart: living expenses, taxes and debt">
    <path d="M70 2 A68 68 0 0 0 70 138 Z" fill="var(--green)"/>
    <path d="M70 2 A68 68 0 0 1 138 70 L70 70 Z" fill="var(--navy)"/>
    <path d="M70 70 L138 70 A68 68 0 0 1 70 138 Z" fill="var(--navy)"/>
    <line x1="70" y1="70" x2="140" y2="70" stroke="#fff" stroke-width="2.5"/>
    <text x="16" y="65" font-family="Roboto,sans-serif" font-size="7.5" fill="#fff">Living</text>
    <text x="16" y="75" font-family="Roboto,sans-serif" font-size="7.5" fill="#fff">Expenses</text>
    <text x="89" y="42" font-family="Roboto,sans-serif" font-size="7.5" fill="#fff">Taxes</text>
    <text x="88" y="101" font-family="Roboto,sans-serif" font-size="7.5" fill="#fff">Debt</text>
  </svg>
  <div class="abs heading savings-tag">SAVINGS</div>

  <svg class="abs" style="left:160px;top:566px" width="28" height="12" viewBox="0 0 28 12"><path d="M1 6h25M20 1l6 5-6 5" stroke="#1b1f24" stroke-width="1.6" fill="none"/></svg>
  <ul class="abs goals">
    <li>Retirement Savings</li>
    <li>Children's Education</li>
    <li>Proper Protection</li>
    <li>Freedom From Debt</li>
  </ul>
  <svg class="abs" style="left:323px;top:566px" width="28" height="12" viewBox="0 0 28 12"><path d="M1 6h25M20 1l6 5-6 5" stroke="#1b1f24" stroke-width="1.6" fill="none"/></svg>

  <div class="abs partners">
    <div class="partner">Maplecrest</div>
    <div class="partner">Harbourlife</div>
    <div class="partner">Sunmeadow Financial</div>
    <div class="partner">Granite Mutual</div>
    <div class="partner">Northpine</div>
    <div class="partner">Redstone Insurance</div>
    <div class="partner">Belvia</div>
    <div class="partner">Bluefield Insurance</div>
    <div class="partner">Unity Co-op</div>
    <div class="partner">Vantor</div>
  </div>
  <svg class="abs" style="left:427px;top:681px" width="10" height="14" viewBox="0 0 10 14"><path d="M5 0v12M1 8l4 5 4-5" stroke="#1b1f24" stroke-width="1.2" fill="none"/></svg>
  <div class="abs heading payus">PAY US</div>
</section>

<section class="page page--right">
  <div class="abs rule"></div>
  <h2 class="abs heading rule__title">RULE OF 72</h2>

  <div class="abs growth" style="left:18px">
    <div class="growth__table">
      <div class="growth__head"><span>AGE</span><span>4%</span></div>
      <div class="growth__row"><span>29</span><span>$10,000</span></div>
      <div class="growth__row"><span>47</span><span>$20,000</span></div>
      <div class="growth__row"><span>65</span><span>$40,000</span></div>
    </div>
    <div class="growth__note">MONEY DOUBLES<br>EVERY 18 YEARS</div>
  </div>
  <div class="abs growth" style="left:141px">
    <div class="growth__table">
      <div class="growth__head"><span>AGE</span><span>6%</span></div>
      <div class="growth__row"><span>29</span><span>$10,000</span></div>
      <div class="growth__row"><span>41</span><span>$20,000</span></div>
      <div class="growth__row"><span>53</span><span>$40,000</span></div>
      <div class="growth__row"><span>65</span><span>$80,000</span></div>
    </div>
    <div class="growth__note">MONEY DOUBLES<br>EVERY 12 YEARS</div>
  </div>
  <div class="abs growth" style="left:264px">
    <div class="growth__table">
      <div class="growth__head"><span>AGE</span><span>8%</span></div>
      <div class="growth__row"><span>29</span><span>$10,000</span></div>
      <div class="growth__row"><span>38</span><span>$20,000</span></div>
      <div class="growth__row"><span>47</span><span>$40,000</span></div>
      <div class="growth__row"><span>56</span><span>$80,000</span></div>
      <div class="growth__row"><span>65</span><span>$160,000</span></div>
    </div>
    <div class="growth__note">MONEY DOUBLES<br>EVERY 9 YEARS</div>
  </div>
  <div class="abs growth" style="left:388px">
    <div class="growth__table">
      <div class="growth__head"><span>AGE</span><span>12%</span></div>
      <div class="growth__row"><span>29</span><span>$10,000</span></div>
      <div class="growth__row"><span>35</span><span>$20,000</span></div>
      <div class="growth__row"><span>41</span><span>$40,000</span></div>
      <div class="growth__row"><span>47</span><span>$80,000</span></div>
      <div class="growth__row"><span>53</span><span>$160,000</span></div>
      <div class="growth__row"><span>59</span><span>$320,000</span></div>
      <div class="growth__row"><span>65</span><span>$640,000</span></div>
    </div>
    <div class="growth__note">MONEY DOUBLES<br>EVERY 6 YEARS</div>
  </div>

  <h2 class="abs heading taxes__title">TAXES</h2>
  <div class="abs taxes__art" role="img" aria-label="Illustration of a laptop, calendar and tax reports with bar charts on a desk"></div>

  <div class="abs taxes__card">
    <div class="abs tax-col" style="left:0;width:132px">
      <h3>HOME</h3>
      <ul><li>Partner with mortgage brokers for best rates</li><li>Mortgage insurance alternatives</li></ul>
      <span class="tax-tag">SELL</span>
    </div>
    <div class="abs tax-col" style="left:132px;width:100px">
      <h3>RRSP</h3>
      <ul><li>Tax deduction</li><li>Tax deferred</li></ul>
      <span class="tax-tag">SELL</span>
    </div>
    <div class="abs tax-col" style="left:232px;width:118px">
      <h3>TFSA</h3>
      <ul><li>No tax deductions</li><li>Tax free growth</li><li>2009 - $95,000</li><li>Limit 2023 - $7,000/yr</li></ul>
      <span class="tax-tag">0% TAX</span>
    </div>
    <div class="abs tax-col" style="left:350px;width:128px">
      <h3>PERM LIFE</h3>
      <ul><li>No tax deduction</li><li>Qualify</li><li>Tax deferred growth</li></ul>
      <span class="tax-tag">0% TAX</span>
    </div>
  </div>

  <div class="abs taxes__foot">
    <svg class="abs" style="left:23px;top:15px" width="22" height="26" viewBox="0 0 22 26"><path d="M11 1l9 3.5v7c0 7-4.5 10.5-9 13-4.5-2.5-9-6-9-13v-7z" fill="var(--green)"/><path d="M6.5 13l3.5 3.5 6-6" stroke="#fff" stroke-width="2.2" fill="none"/></svg>
    <div class="abs foot-rule" style="left:57px"></div>
    <div class="abs foot-text" style="left:74px">Life insurance illness<br>critical / disability</div>
    <svg class="abs" style="left:289px;top:15px" width="28" height="26" viewBox="0 0 28 26"><rect x="2" y="6" width="14" height="5" rx="1" fill="var(--green)"/><rect x="2" y="12" width="14" height="5" rx="1" fill="var(--green)"/><rect x="2" y="18" width="14" height="5" rx="1" fill="var(--green)"/><circle cx="20" cy="10" r="6" fill="none" stroke="var(--green)" stroke-width="2"/></svg>
    <div class="abs foot-rule" style="left:331px"></div>
    <div class="abs foot-text" style="left:347px">Debt management<br>cash flow</div>
  </div>
</section>

</body>
</html>
```